Create a business promotion flyer to leave in customer mailboxes. We are a bulk petroleum supplier, servicing any industry that requires diesel. Base in griffith NSW, servicing griffith area and surrounds.

Business Name - Terra Diesel
Fuel@terradiesel-example.com.au
Owen - 0491 570 362 ohartley@terradiesel-example.com.au
Liam - 0491 570 718 lprosser@terradiesel-example.com.au
Simon - 0491 570 905 skenway@terradiesel-example.com.au
Office 02 5550 1734

Bulk Fuel deliveries.
Oils & lubricants
Local Family owned business

```html
<!DOCTYPE html>
<html lang="en">
<head>
<meta charset="utf-8">
<title>Terra Diesel – Bulk Fuel Flyer</title>
<link rel="stylesheet" href="https://fonts.googleapis.com/css2?family=Bebas+Neue&family=Poppins:wght@400;500;600;700&display=swap">
<style>
  :root {
    --red: #ec1c24;
    --charcoal: #231f20;
    --ink: #2b2b2b;
    --white: #ffffff;
    --backdrop: #58595b;
    --sky-top: #b9c9e4;
    --sky-low: #e9eef6;
    --shed: #8b96a4;
  }
  * { box-sizing: border-box; margin: 0; padding: 0; }
  html, body { width: 1051px; height: 1200px; overflow: hidden; }
  body { background: var(--backdrop); position: relative; font-family: "Poppins", sans-serif; }

  .flyer { position: absolute; left: 174px; top: 154px; width: 702px; height: 909px; background: var(--white); overflow: hidden; }

  .hero { position: absolute; left: 0; top: 0; width: 702px; height: 293px;
    background: linear-gradient(180deg, var(--sky-top) 0%, var(--sky-low) 45%, var(--shed) 80%, #5a6370 100%); }
  .brand { position: absolute; left: 57px; top: 70px; display: flex; align-items: center; gap: 10px; }
  .brand-dot { width: 22px; height: 22px; border-radius: 50%; background: var(--red); }
  .brand-name { font-weight: 600; font-size: 34px; color: var(--red); letter-spacing: -0.5px; }
  .tagline-box { position: absolute; left: 510px; top: 0; width: 166px; height: 208px; background: var(--red);
    color: var(--white); font-size: 18.5px; line-height: 24px; text-align: center; padding-top: 47px; font-weight: 500; }
  .tagline-box strong { font-weight: 700; }

  .services { position: absolute; left: 0; top: 293px; width: 702px; height: 368px; background: var(--charcoal); }
  .headline { position: absolute; left: 59px; top: 62px; font-family: "Bebas Neue", sans-serif; font-weight: 400;
    font-size: 84px; line-height: 64.5px; color: var(--white); letter-spacing: 0.3px; white-space: nowrap; }
  .headline .accent { color: var(--red); }

  .timeline { position: absolute; left: 430px; top: 75px; width: 1px; height: 222px; background: var(--red); }
  .service-icon { position: absolute; left: 400px; width: 62px; height: 62px; border-radius: 50%; background: var(--red); }
  .service-icon svg { width: 62px; height: 62px; }
  .service { position: absolute; left: 483px; color: var(--white); }
  .service h3 { font-size: 21px; line-height: 25px; font-weight: 700; }
  .service p { font-size: 12.5px; line-height: 16.5px; margin-top: 6px; }

  .contacts { position: absolute; left: 0; top: 661px; width: 702px; height: 188px; }
  .cta { position: absolute; left: 59px; top: 28px; font-size: 27px; line-height: 35px; font-weight: 600; color: var(--ink); }
  .cta .accent { color: var(--red); }
  .cta small { display: block; font-size: 14px; line-height: 20px; font-weight: 500; margin-top: 4px; }
  .person { position: absolute; font-size: 17px; line-height: 20px; color: var(--ink); }
  .person .row { display: flex; align-items: center; gap: 7px; white-space: nowrap; }
  .person .name { font-weight: 500; }
  .person .phone { font-weight: 600; }
  .person .email { font-size: 9.6px; letter-spacing: -0.1px; margin-top: 3px; }
  .person svg { width: 10px; height: 10px; flex: none; fill: var(--red); }

  .email-band { position: absolute; left: 0; top: 849px; width: 702px; height: 60px; background: var(--red);
    display: flex; align-items: center; padding-left: 67px; gap: 10px; color: var(--white); }
  .email-band .lead { font-size: 14.5px; font-weight: 500; }
  .email-band .mail-dot { width: 27px; height: 27px; border-radius: 50%; background: var(--charcoal); display: flex; align-items: center; justify-content: center; }
  .email-band .mail-dot svg { width: 13px; height: 10px; }
  .email-band .address { font-size: 18.5px; font-weight: 700; }
</style>
</head>
<body>
<svg width="0" height="0" style="position:absolute">
  <defs>
    <symbol id="ico-person" viewBox="0 0 10 10"><circle cx="5" cy="2.6" r="2.3"/><path d="M0.5 10 C0.8 6.2 9.2 6.2 9.5 10 Z"/></symbol>
    <symbol id="ico-phone" viewBox="0 0 10 10"><path d="M2.2 0.6 L4 2.8 L3 4 C3.6 5.4 4.6 6.4 6 7 L7.2 6 L9.4 7.8 L8.2 9.4 C4.4 9 1 5.6 0.6 1.8 Z"/></symbol>
    <symbol id="ico-mail" viewBox="0 0 10 8"><path d="M0 0 H10 V8 H0 Z M0.8 0.8 L5 4.4 L9.2 0.8" stroke="#fff" stroke-width="0.8"/></symbol>
    <symbol id="ico-office" viewBox="0 0 10 10"><path d="M1 10 V1 H6 V10 Z M6 4 H9 V10 H6" fill="none" stroke="#ec1c24" stroke-width="0.9"/></symbol>
  </defs>
</svg>

<main class="flyer">
  <header class="hero" role="img" aria-label="Photo of a fuel depot shed under a cloudy blue sky with a white road-train fuel tanker parked in front">
    <div class="brand"><span class="brand-dot"></span><span class="brand-name">Terra Diesel</span></div>
    <div class="tagline-box">Reliable bulk<br>fuel supply<br>across <strong>Griffith</strong><br>and surrounds</div>
  </header>

  <section class="services">
    <h1 class="headline"><span class="accent">Fuel for</span><br>Farming,<br>Transport<br>&amp; Industry</h1>

    <div class="timeline"></div>
    <div class="service-icon" style="top:44px">
      <svg viewBox="0 0 62 62" fill="none" stroke="#fff" stroke-width="1.6"><rect x="20" y="16" width="16" height="30" rx="1.5"/><rect x="23" y="20" width="10" height="6"/><path d="M28 30 C25 34 25 37 28 37 C31 37 31 34 28 30Z"/><path d="M36 22 L41 26 V40 C41 42 44 42 44 40 V28"/><path d="M18 46 H38"/></svg>
    </div>
    <div class="service" style="top:38px"><h3>Bulk Fuel<br>deliveries.</h3><p>Reliable diesel supply<br>for any industry.</p></div>

    <div class="service-icon" style="top:155px">
      <svg viewBox="0 0 62 62" fill="none" stroke="#fff" stroke-width="1.6"><path d="M22 22 H40 V46 H22 Z"/><path d="M26 22 L22 16 L19 19 L22 22"/><path d="M28 30 C25 34 25 37 28 37 C31 37 31 34 28 30Z"/><rect x="34" y="28" width="3" height="8" rx="1.5"/><path d="M22 41 H40"/></svg>
    </div>
    <div class="service" style="top:141px"><h3>Oils &amp;<br>lubricants</h3><p>Quality products to keep<br>your equipment<br>performing at its best.</p></div>

    <div class="service-icon" style="top:265px">
      <svg viewBox="0 0 62 62" fill="none" stroke="#fff" stroke-width="1.6"><circle cx="21" cy="25" r="3.5"/><circle cx="31" cy="25" r="3.5"/><circle cx="41" cy="25" r="3.5"/><path d="M14 38 C14 31 28 31 28 38"/><path d="M24 42 C24 34 38 34 38 42"/><path d="M34 38 C34 31 48 31 48 38"/></svg>
    </div>
    <div class="service" style="top:262px"><h3>Local Family<br>owned business</h3><p>Proudly supporting our<br>local community.</p></div>
  </section>

  <section class="contacts">
    <div class="cta"><span class="accent">Need fuel</span><br>for your<br>operation?<small>Contact Us</small></div>

    <div class="person" style="left:263px; top:25px">
      <div class="row name"><svg><use href="#ico-person"/></svg>Owen</div>
      <div class="row phone"><svg><use href="#ico-phone"/></svg>0491 570 362</div>
      <div class="row email"><svg><use href="#ico-mail"/></svg>ohartley@terradiesel-example.com.au</div>
    </div>
    <div class="person" style="left:482px; top:27px">
      <div class="row name"><svg><use href="#ico-person"/></svg>Liam</div>
      <div class="row phone"><svg><use href="#ico-phone"/></svg>0491 570 718</div>
      <div class="row email"><svg><use href="#ico-mail"/></svg>lprosser@terradiesel-example.com.au</div>
    </div>
    <div class="person" style="left:263px; top:111px">
      <div class="row name"><svg><use href="#ico-person"/></svg>Simon</div>
      <div class="row phone"><svg><use href="#ico-phone"/></svg>0491 570 905</div>
      <div class="row email"><svg><use href="#ico-mail"/></svg>skenway@terradiesel-example.com.au</div>
    </div>
    <div class="person" style="left:482px; top:123px">
      <div class="row name"><svg style="width:14px;height:14px"><use href="#ico-office"/></svg>Office</div>
      <div class="row phone"><svg><use href="#ico-phone"/></svg>02 5550 1734</div>
    </div>
  </section>

  <footer class="email-band">
    <span class="lead">Have questions? Email us at:</span>
    <span class="mail-dot"><svg viewBox="0 0 10 8" fill="#fff"><path d="M0 0 H10 V8 H0 Z"/><path d="M0.6 0.6 L5 4.2 L9.4 0.6" stroke="#231f20" stroke-width="0.9" fill="none"/></svg></span>
    <span class="address">Fuel@terradiesel-example.com.au</span>
  </footer>
</main>
</body>
</html>
```